New letter head for Air Conditioning business

We need a new professional letter head design to suit our new re-branded air conditioning business. Our new logo is attached

```html
<!DOCTYPE html>
<html lang="en">
<head>
<meta charset="utf-8">
<title>Boreal Air Conditioning &amp; Refrigeration – Letterhead</title>
<link href="https://fonts.googleapis.com/css2?family=Open+Sans:wght@400;600;700&display=swap" rel="stylesheet">
<style>
  :root {
    --backdrop: #e9e9ea;
    --paper: #ffffff;
    --ink: #5a5a5c;
    --ink-dark: #3b3b3d;
    --brand-red: #ee6352;
    --brand-green: #4dbb74;
    --band-dark: #3a3a3c;
    --sig-tone: #d9d9db;
  }
  * { margin: 0; padding: 0; box-sizing: border-box; }
  html, body { width: 1200px; height: 795px; overflow: hidden; }
  body {
    background: var(--backdrop);
    font-family: "Open Sans", Arial, sans-serif;
    color: var(--ink);
    position: relative;
  }
  .letterhead {
    position: absolute;
    left: 333px; top: 20px;
    width: 534px; height: 755px;
    background: var(--paper);
    box-shadow: 0 2px 10px rgba(0,0,0,0.12);
    overflow: hidden;
  }
  .brand {
    position: absolute; left: 48px; top: 52px;
    display: flex; align-items: center; gap: 8px;
  }
  .brand-dot { width: 14px; height: 14px; border-radius: 50%; background: var(--brand-red); }
  .brand-name { font-size: 22px; font-weight: 600; letter-spacing: 3px; color: var(--ink-dark); }
  .contact-list {
    position: absolute; right: 40px; top: 40px;
    list-style: none; font-size: 7px; line-height: 11px; color: var(--ink-dark);
  }
  .contact-list li { display: flex; align-items: center; gap: 4px; }
  .contact-list svg { width: 7px; height: 7px; }
  .letter-body {
    position: absolute; left: 48px; top: 150px; width: 360px;
    font-size: 8.5px; line-height: 12.5px;
  }
  .letter-date { margin-bottom: 14px; }
  .recipient { margin-bottom: 12px; }
  .salutation { font-weight: 700; color: var(--ink-dark); margin-bottom: 10px; }
  .letter-body p.para { margin-bottom: 12px; }
  .signature {
    position: absolute; left: 420px; top: 440px; width: 70px; height: 28px;
    background: var(--sig-tone); border-radius: 4px; opacity: .6;
  }
  .footer-band { position: absolute; left: 0; bottom: 0; width: 534px; height: 300px; }
  .footer-text {
    position: absolute; left: 48px; bottom: 22px;
    font-size: 10px; line-height: 14px; color: #ffffff;
  }
  .footer-text .name-red { color: var(--brand-red); font-weight: 600; }
  .footer-text .name-green { color: var(--brand-green); }
</style>
</head>
<body>
  <main class="letterhead">
    <header class="brand">
      <span class="brand-dot"></span>
      <span class="brand-name">BOREAL</span>
    </header>

    <ul class="contact-list">
      <li><svg viewBox="0 0 10 10"><circle cx="5" cy="5" r="5" fill="var(--brand-red)"/></svg>000 0134 567 890</li>
      <li><svg viewBox="0 0 10 10"><circle cx="5" cy="5" r="5" fill="var(--brand-green)"/></svg>000 0134 567 891</li>
      <li><svg viewBox="0 0 10 10"><circle cx="5" cy="5" r="5" fill="var(--brand-red)"/></svg>info@borealcooling.com</li>
      <li><svg viewBox="0 0 10 10"><circle cx="5" cy="5" r="5" fill="var(--brand-green)"/></svg>www.borealcooling.com</li>
    </ul>

    <section class="letter-body">
      <p class="letter-date">January 12, 2014</p>
      <p class="recipient">Mr. John Doe<br>President<br>AA Corporation<br>111 Street Name, Suite#<br>City, State, 12345</p>
      <p class="salutation">Dear Mr. John,</p>
      <p class="para">Lorem Ipsum is simply dummy text of the printing and typesetting industry. Lorem Ipsum has been the industry's standard dummy text ever since the 1500s, when an unknown printer took a galley of type and scrambled it to make a type specimen book. It has survived not only five centuries, but also the leap into electronic typesetting, remaining essentially unchanged.</p>
      <p class="para">The standard chunk of Lorem Ipsum used since the 1500s is reproduced below for those interested. Sections 1.10.32 and 1.10.33 from "de Finibus Bonorum et Malorum" by Cicero are also reproduced in their exact original form, accompanied by English versions from the 1914 translation by H. Rackham.</p>
      <p class="para">Lorem Ipsum is simply dummy text of the printing and typesetting industry. Lorem Ipsum has been the industry's standard dummy text ever since the 1500s, when an unknown printer took a galley of type and scrambled it to make a type specimen book. It has survived not only five centuries, but also the leap into electronic typesetting, remaining essentially unchanged. It was popularised in the</p>
    </section>

    <div class="signature" role="img" aria-label="Handwritten signature"></div>

    <svg class="footer-band" viewBox="0 0 534 300" preserveAspectRatio="none" aria-hidden="true">
      <path transform="translate(0,-24)" d="M0,205 C120,190 250,185 350,150 C450,115 510,60 534,0" fill="none" stroke="var(--brand-green)" stroke-width="5"/>
      <path transform="translate(0,-12)" d="M0,205 C120,190 250,185 350,150 C450,115 510,60 534,0" fill="none" stroke="var(--brand-red)" stroke-width="7"/>
      <path d="M0,205 C120,190 250,185 350,150 C450,115 510,60 534,0 L534,300 L0,300 Z" fill="var(--band-dark)"/>
    </svg>

    <footer class="footer-text">
      <p><span class="name-red">Boreal</span> <span class="name-green">Air Conditioning &amp; Refrigeration</span></p>
      <p>Suite 102 Street name, State, Zip 2034, Country</p>
    </footer>
  </main>
</body>
</html>
```